Business card design for holistic health care clinic

We need a double-sided business card design for our holistic health care clinic that integrates our logo design and also its color scheme. My business is called Valmira. It is an integrative medicine clinic. You have already done the logo for me. Please ensure an elegant and upscale design that is not cluttered, but still has all the necessary information (please see below for details).

Target Market(s)

Wellness, fitness, rehabilitation for educated, well-traveled open-minded clients who are focused on natural, organic, balanced and preventive healthcare and lifestyle.

Industry/Entity Type

Medical

Contact Information for Business Card

Modern, clean.

Number of Pages Required

1 page

Font styles to use
Serif
Sans Serif

Colors

Designer to choose colors to be used in the design.

Requirements
Must have
• Logo on one side, all other information on the other side.
• Other information should include:
• Tobias Wrenfeld - DOE, CPT, LMT
• 4100 East Marrow Drive
• Austin, TX 78119
• 512 555 0148
• 818 555 0192
• info@ValmiraHealth.example
• t.wrenfeld@ValmiraHealth.example
Nice to have
• Darker background on front - but not totally black - shaded/dark gray.

```html
<!DOCTYPE html>
<html lang="en">
<head>
<meta charset="utf-8">
<title>Valmira – Business Card</title>
<link rel="stylesheet" href="https://fonts.googleapis.com/css2?family=Nunito:wght@800&family=Roboto:ital,wght@0,400;1,400&family=Roboto+Condensed:wght@700&display=swap">
<style>
  :root {
    --brand-blue: #1a8fd0;
    --panel-blue: #0a8fce;
    --card-dark: #2b2c2e;
    --card-white: #ffffff;
    --stage: #e9e9e7;
    --text-light: #ffffff;
  }
  * { margin: 0; padding: 0; box-sizing: border-box; }
  html, body { width: 1200px; height: 960px; overflow: hidden; }
  body { background: var(--stage); position: relative; font-family: "Roboto", sans-serif; }

  .card {
    position: absolute;
    left: 320px;
    width: 600px;
    height: 342px;
    border-radius: 18px;
    overflow: hidden;
    box-shadow: 0 4px 12px rgba(0,0,0,0.25);
  }

  /* Front side */
  .card-front { top: 108px; background: var(--card-dark); text-align: center; }
  .brand-name {
    position: absolute; left: 0; right: 0; top: 138px;
    font-family: "Nunito", sans-serif; font-weight: 800;
    font-size: 68px; line-height: 1; letter-spacing: 1px;
    color: var(--brand-blue);
  }
  .brand-sub {
    position: absolute; left: 0; right: 0; top: 204px;
    font-family: "Nunito", sans-serif; font-weight: 800;
    font-size: 18px; color: var(--brand-blue);
  }
  .front-tagline {
    position: absolute; left: 0; right: 0; top: 270px;
    display: flex; align-items: center; justify-content: center; gap: 8px;
    font-style: italic; font-size: 17px; color: var(--text-light);
  }
  .front-tagline .rule { width: 110px; height: 1px; }
  .front-tagline .rule-left { background: linear-gradient(to right, transparent, var(--brand-blue)); }
  .front-tagline .rule-right { background: linear-gradient(to left, transparent, var(--brand-blue)); }

  /* Back side */
  .card-back { top: 493px; background: var(--card-white); }
  .back-panel { position: absolute; inset: 0; }
  .back-brand { position: absolute; left: 34px; top: 58px; }
  .back-brand .brand-name-small {
    font-family: "Nunito", sans-serif; font-weight: 800;
    font-size: 42px; line-height: 1; color: var(--brand-blue);
  }
  .back-brand .brand-sub-small {
    font-family: "Nunito", sans-serif; font-weight: 800;
    font-size: 12.5px; color: var(--brand-blue); margin-top: 5px;
  }
  .contact-list {
    position: absolute; right: 24px; top: 146px;
    list-style: none; color: var(--text-light); font-size: 14.5px; text-align: right;
  }
  .contact-list li { display: flex; align-items: center; justify-content: flex-end; gap: 9px; height: 19.3px; }
  .contact-list svg { width: 13px; height: 13px; fill: var(--text-light); }
  .address { position: absolute; right: 44px; top: 228px; color: var(--text-light); font-size: 14.5px; line-height: 18px; text-align: right; }
  .person {
    position: absolute; right: 24px; top: 272px; color: var(--text-light);
    font-family: "Roboto Condensed", sans-serif; font-weight: 700; font-size: 20px;
  }
  .person .creds { font-size: 11px; }
  .back-tagline { position: absolute; right: 24px; top: 308px; color: var(--text-light); font-size: 14.5px; }
</style>
</head>
<body>

<section class="card card-front">
  <div class="brand-name">VALMIRA</div>
  <div class="brand-sub">Integrative Holistic Medicine</div>
  <div class="front-tagline">
    <span class="rule rule-left"></span>
    <span>helping the body help itself</span>
    <span class="rule rule-right"></span>
  </div>
</section>

<section class="card card-back">
  <svg class="back-panel" viewBox="0 0 600 342" preserveAspectRatio="none" aria-hidden="true">
    <path d="M388,0 C402,70 380,140 300,205 C230,262 150,312 100,342 L600,342 L600,0 Z" fill="var(--panel-blue)"/>
  </svg>

  <div class="back-brand">
    <div class="brand-name-small">VALMIRA</div>
    <div class="brand-sub-small">Integrative Holistic Medicine</div>
  </div>

  <ul class="contact-list">
    <li>512 555 0148
      <svg viewBox="0 0 16 16"><path d="M3.5 1l2.5 3-1.5 2c1 2 3 4 5 5l2-1.5 3 2.5-1.5 2.5C7 15 1 9 1 2.5z"/></svg>
    </li>
    <li>818 555 0192
      <svg viewBox="0 0 16 16"><path d="M4 0h8v16H4zM5.5 2v10h5V2zM7 13.2h2v1.3H7z" fill-rule="evenodd"/></svg>
    </li>
    <li>t.wrenfeld@ValmiraHealth.example
      <svg viewBox="0 0 16 16"><path d="M1 3h14v10H1zM2 4.5v.3l6 4 6-4v-.3zM2 6.2V12h12V6.2l-6 4z" fill-rule="evenodd"/></svg>
    </li>
    <li>www.ValmiraHealth.example
      <svg viewBox="0 0 16 16"><path d="M8 1a7 7 0 100 14A7 7 0 008 1zm0 1.5c1 1 1.6 2.6 1.8 4.5H6.2C6.4 5.1 7 3.5 8 2.5zM2.6 9h3.6c.2 1.9.8 3.5 1.8 4.5A5.5 5.5 0 012.6 9zm7.2 0h3.6A5.5 5.5 0 018 13.5c1-1 1.6-2.6 1.8-4.5z"/></svg>
    </li>
  </ul>

  <div class="address">4100 East Marrow Drive<br>Austin, TX 78119</div>
  <div class="person">TOBIAS WRENFELD <span class="creds">- DOE, CPT, LMT</span></div>
  <div class="back-tagline">it’s all about you – your health, your objectives</div>
</section>

</body>
</html>
```